New Technology Company is Launching New Products with a New Website

We want to create a 4-page website in WordPress compatible files to launch our site on HostMeadow. The attached files provide our ideas for Products, Services and About Us pages. We believe the content in those files is about right but the actual design is up to the artist that wants to accept this challenge. Additionally we need a fantastic Home page but we have no idea what that looks like. It obviously needs to lead to the other 3 pages but more importantly it needs to capture the interest of our current and future customers.

Details:
1. Please start off using the text descriptions in the example files. If shorter, longer, different descriptions are needed, just let us know.

2. Please feel free to suggest any photos you can find from free or reasonable stock photo services. Picvault and others like them are reasonable. If you find a perfect image, please send us a link and we will buy a license if its affordable. I have paid ~US$10 per image in the past.

3. I have also uploaded our stationery and logo files. We would like the website design to be consistent with the logo and stationery designs. The stationery designs are all in one file.

We have two logos, and would like to see both of them used on the website. One logo shows the letters KRTV in an outlined shield that is read and blue. That logo is used in the stationery and in our draft website design as a header. The other logo shows flames bouncing off a round shield. Perhaps this logo could be used at the bottom of each page on the website, or some other place where it would be fun and creative without diminishing the seriousness of our underlying science and engineering.

4. We are looking for an artist to have some fun with this and propose something creative. We have lots of boring ideas ourselves so we need YOU to do something else! Thank you so much for considering this challenge!

Target Market(s)

People interested in new, high performance fabrics, including consumers, store owners, garment designers and companies like Wolverock or The Ridge Pelt

Coding

Coded - Design and coding required

Font styles to use
Sans Serif

Colors
f04a51
3277b5

Requirements
Must have
• something unforgetable

```html
<!DOCTYPE html>
<html lang="en">
<head>
<meta charset="utf-8">
<title>R.T. Vance and Associates PLLC</title>
<link href="https://fonts.googleapis.com/css2?family=Montserrat:wght@400;600;700&family=Open+Sans:wght@400;600&display=swap" rel="stylesheet">
<style>
:root{
  --red:#f04a51;
  --blue:#3277b5;
  --ink:#2d2d33;
  --body:#6b6b72;
  --footer:#2b2b2e;
  --footer-deep:#1f1f21;
}
*{margin:0;padding:0;box-sizing:border-box}
html,body{width:1200px;height:3520px;overflow:hidden}
body{background:#fff;font-family:"Open Sans",Arial,sans-serif;color:var(--body);position:relative}
h1,h2,h3,.nav,.brand{font-family:"Montserrat",Arial,sans-serif}

.hero{position:absolute;left:0;top:0;width:1200px;height:420px;background:linear-gradient(100deg,#1f2024 0%,#3d3e44 45%,#5a5b61 70%,#2c2d31 100%)}
.hero-photo{position:absolute;left:150px;top:60px;width:420px;height:360px;background:radial-gradient(ellipse at 50% 60%,#6f7076 0%,#45464b 55%,rgba(44,45,49,0) 80%)}
.topbar{position:absolute;left:0;top:0;width:1200px;height:96px;background:rgba(20,20,24,.55)}
.topbar-band{position:absolute;right:0;top:0;width:520px;height:56px;background:var(--blue);clip-path:polygon(40px 0,100% 0,100% 100%,0 100%)}
.brand{position:absolute;left:36px;top:20px;display:flex;align-items:center;gap:12px;color:#fff;font-size:26px;font-weight:700;letter-spacing:1px}
.brand-mark{width:30px;height:30px;border-radius:50%;background:var(--red)}
.callus{position:absolute;left:930px;top:8px;color:#fff;display:flex;align-items:center;gap:10px}
.callus small{display:block;font-size:10px;letter-spacing:1px;opacity:.85}
.callus strong{font-family:"Montserrat",sans-serif;font-size:20px;font-weight:700}
.nav{position:absolute;left:700px;top:62px;display:flex;gap:6px;font-size:11px;font-weight:700;letter-spacing:.5px}
.nav a{color:#fff;text-decoration:none;padding:8px 14px}
.nav a.active{background:var(--red)}
.hero-title{position:absolute;left:660px;top:222px;color:#fff;width:420px}
.hero-title .lead{font-family:"Montserrat",sans-serif;font-size:34px;font-weight:400;display:block}
.hero-title .rest{font-family:"Montserrat",sans-serif;font-size:34px;font-weight:600;letter-spacing:1px;display:block;margin-top:4px}
.hero-title hr{border:0;border-top:2px solid #fff;width:330px;margin-top:14px;opacity:.8}

.card{position:absolute;background:#fff;box-shadow:0 6px 28px rgba(0,0,0,.16);overflow:hidden}
.card .photo{position:relative;display:block;width:100%}
.card svg{display:block}
.copy{position:absolute;width:420px}
.copy h2{font-size:26px;line-height:1.15;font-weight:700;color:var(--ink);letter-spacing:.5px;text-transform:uppercase}
.copy h2 .accent{color:var(--blue);display:block}
.copy p{font-size:13px;line-height:1.65;margin-top:18px}
.credit{position:absolute;left:8px;bottom:6px;color:#fff;font-size:10px;font-weight:600}

.footer{position:absolute;left:0;top:3048px;width:1200px;height:472px;background:var(--footer);color:#c9c9cf}
.footer .brand-foot{position:absolute;left:60px;top:80px;display:flex;align-items:center;gap:14px;color:#fff;font-family:"Montserrat",sans-serif;font-weight:700;font-size:30px}
.footer .brand-foot span.mark{width:40px;height:40px;border-radius:50%;background:var(--blue)}
.fcol{position:absolute;top:60px;font-size:12px;line-height:1.9}
.fcol h3{color:#fff;font-size:13px;font-weight:700;margin-bottom:12px;letter-spacing:.5px}
.fcol .row{display:flex;align-items:center;gap:10px}
.social .row{margin-bottom:10px}
.social .dot{width:22px;height:22px;border-radius:50%;background:var(--blue)}
.copyright{position:absolute;left:0;bottom:0;width:1200px;height:52px;background:var(--footer-deep);color:#8e8e95;font-size:11px;text-align:center;line-height:52px}
</style>
</head>
<body>

<header class="hero">
  <div class="hero-photo" role="img" aria-label="Mountaineer with ski poles climbing a snowy slope"></div>
  <div class="topbar"></div>
  <div class="topbar-band"></div>
  <div class="brand"><span class="brand-mark"></span>KRTV</div>
  <div class="callus">
    <svg width="22" height="22" viewBox="0 0 24 24"><path fill="#fff" d="M6.6 10.8a15 15 0 0 0 6.6 6.6l2.2-2.2c.3-.3.7-.4 1-.2 1.1.4 2.3.6 3.6.6.6 0 1 .4 1 1V20c0 .6-.4 1-1 1A17 17 0 0 1 3 4c0-.6.4-1 1-1h3.5c.6 0 1 .4 1 1 0 1.3.2 2.5.6 3.6.1.3 0 .7-.2 1z"/></svg>
    <div><small>CALL US</small><strong>555.014.2200</strong></div>
  </div>
  <nav class="nav"><a class="active">HOME</a><a>ABOUT US</a><a>SERVICES</a><a>CONTACT US</a></nav>
  <h1 class="hero-title"><span class="lead">R.T. Vance and</span><span class="rest">ASSOCIATES PLLC</span><hr></h1>
</header>

<div class="card" style="left:172px;top:592px;width:356px;height:232px">
  <div class="photo" role="img" aria-label="Glowing red dome of insulation tiles under heat test" style="height:112px;background:radial-gradient(ellipse at 50% 40%,#e0332c 0%,#8c1714 40%,#1a0b0b 75%)"><span class="credit">Credit: Space Agency</span></div>
  <svg width="356" height="120" viewBox="0 0 356 120">
    <text x="178" y="12" font-size="7" text-anchor="middle" fill="#444">THERMAL CONDUCTIVITY</text>
    <line x1="30" y1="18" x2="30" y2="104" stroke="#999"/><line x1="30" y1="104" x2="340" y2="104" stroke="#999"/>
    <path d="M30 104 L30 80 C120 70 220 50 340 22 L340 104 Z" fill="#d8282b"/>
    <path d="M30 104 L30 92 C140 88 240 72 340 52 L340 104 Z" fill="#2b5fb0"/>
    <text x="185" y="116" font-size="7" text-anchor="middle" fill="#666">Temperature</text>
  </svg>
</div>
<div class="copy" style="left:652px;top:660px">
  <h2><span class="accent">High – Temperature</span>Insulation</h2>
  <p>KRTV has been working on aerospace applications of high temperature insulations since the National Aerospace Plane was proposed by President Harlan Doyle. Back then we used gold and platinum to block heat. Today we make insulations that are much more affordable, more efficient and more reliable in Thermal Protection Systems.</p>
  <p>If this is what you need, contact us and ask about our Opacified Fibrous Insulation (OFI).</p>
</div>

<div class="copy" style="left:172px;top:1316px">
  <h2><span class="accent">Aerogel</span>Insulations</h2>
  <p>KRTV has developed aerogel insulations that are thin, flexible and more than twice as warm as goose down. Although we developed these insulations for the Space Agency to take payloads to Mars, we are very excited about their more earthly applications from cold weather clothing to industrial pipelines.</p>
  <p>If this is what you need, contact us and ask about our Fiber Reinforced Insulation with Aerogel (FRIA).</p>
</div>
<div class="card" style="left:660px;top:1340px;width:412px;height:470px">
  <div class="photo" role="img" aria-label="Skier in blue jacket climbing a snowy ridge under blue sky" style="height:170px;background:linear-gradient(180deg,#3f7fc4 0%,#8fb8e0 55%,#eef2f6 100%)"></div>
  <svg width="412" height="300" viewBox="0 0 412 300">
    <text x="16" y="150" font-size="8" fill="#555" transform="rotate(-90 16 150)">R-value / inch</text>
    <line x1="40" y1="20" x2="40" y2="260" stroke="#999"/><line x1="40" y1="260" x2="396" y2="260" stroke="#999"/>
    <g stroke="#e6e6e6"><line x1="40" y1="68" x2="396" y2="68"/><line x1="40" y1="116" x2="396" y2="116"/><line x1="40" y1="164" x2="396" y2="164"/><line x1="40" y1="212" x2="396" y2="212"/></g>
    <rect x="62" y="105" width="36" height="155" fill="#2b5fb0"/>
    <rect x="132" y="172" width="36" height="88" fill="#c9302c"/>
    <rect x="202" y="199" width="36" height="61" fill="#6da33a"/>
    <rect x="272" y="73" width="36" height="187" fill="#7a4fa8"/>
    <rect x="342" y="47" width="36" height="213" fill="#2fb3c7"/>
    <g font-size="8" fill="#555" text-anchor="middle"><text x="80" y="276">Goose</text><text x="150" y="276">Wool</text><text x="220" y="276">Fleece</text><text x="290" y="276">Aerogel</text><text x="360" y="276">FRIA</text></g>
  </svg>
</div>

<div class="card" style="left:172px;top:1844px;width:356px;height:376px">
  <div class="photo" role="img" aria-label="Wildfire burning through trees at night" style="height:190px;background:radial-gradient(ellipse at 60% 70%,#f47a1f 0%,#b8320f 35%,#2a0b05 75%)"></div>
  <svg width="356" height="186" viewBox="0 0 356 186">
    <text x="110" y="16" font-size="7" fill="#444">CALIBRATED TEST FIRE</text>
    <line x1="30" y1="22" x2="30" y2="160" stroke="#999"/><line x1="30" y1="160" x2="340" y2="160" stroke="#999"/>
    <path d="M30 160 C80 130 160 80 300 26 L300 160 Z" fill="#d8282b"/>
    <path d="M30 160 C90 146 170 106 300 66 L300 160 Z" fill="#2aa84a"/>
    <path d="M30 160 C100 154 180 132 300 112 L300 160 Z" fill="#2b5fb0"/>
    <text x="185" y="176" font-size="7" text-anchor="middle" fill="#666">Time (seconds)</text>
  </svg>
</div>
<div class="copy" style="left:652px;top:1928px">
  <h2><span class="accent">Fire Resistant</span>Fabrics</h2>
  <p>KRTV developed fire resistant fabrics and insulation blankets that provide various levels of protection for fire fighters surviving a burn over. The current FS-20 fire shelter has saved many lives and prevented many injuries, but the tragic loss of 19 Ridgeline Hot Shots in 2013 motivated us to develop better fire shelters for today's wild fires that burn hotter and longer than those of 20 years ago.</p>
  <p>If this is what you need, contact us and ask for the KRTV 1000-T, KRTV-3-T and KRTV-M-I fabrics.</p>
</div>

<div class="copy" style="left:172px;top:2650px">
  <h2><span class="accent">Aerodynamic</span>Fabrics</h2>
  <p>KRTV developed and patented aerodynamic fabrics, and measured the drag reduction on bicycles in a wind tunnel.</p>
  <p>If you need to go faster or reduce energy costs, contact us about our Drag eFabric fabrics.</p>
</div>
<div class="card" style="left:660px;top:2528px;width:400px;height:452px">
  <div role="img" aria-label="Road cyclist in racing kit riding on an open road" style="position:absolute;inset:0;background:linear-gradient(180deg,#9fc3e6 0%,#d7e6f2 45%,#9a9a94 80%,#6d6d68 100%)"></div>
  <svg style="position:absolute;left:12px;top:12px" width="150" height="428" viewBox="0 0 150 428">
    <rect width="150" height="428" fill="#fff" opacity=".82"/>
    <g font-family="Open Sans,sans-serif" font-size="10" fill="#333">
      <text x="10" y="22" font-weight="600">Aero TT Helmet</text><text x="10" y="36">47 Sec</text>
      <text x="10" y="76" font-weight="600">TT Suit</text><text x="10" y="90">156 Sec</text>
      <text x="10" y="130" font-weight="600">Wind Tunnel Positioning</text><text x="10" y="144">96 Sec</text>
      <text x="10" y="184" font-weight="600">Aerobars</text><text x="10" y="198">120 Sec</text>
      <text x="10" y="238" font-weight="600">Aero Frame</text><text x="10" y="252">77 Sec</text>
      <text x="10" y="292" font-weight="600">Shoe Covers</text><text x="10" y="306">30 Sec</text>
      <text x="10" y="346" font-weight="600">Race Disc</text><text x="10" y="360">64 Sec</text>
    </g>
    <g stroke="#ccc"><line x1="10" y1="54" x2="140" y2="54"/><line x1="10" y1="108" x2="140" y2="108"/><line x1="10" y1="162" x2="140" y2="162"/><line x1="10" y1="216" x2="140" y2="216"/><line x1="10" y1="270" x2="140" y2="270"/><line x1="10" y1="324" x2="140" y2="324"/></g>
  </svg>
</div>

<footer class="footer">
  <div class="brand-foot"><span class="mark"></span>KRTV</div>
  <div class="fcol" style="left:440px">
    <h3>CONTACT US</h3>
    <div class="row"><svg width="12" height="14" viewBox="0 0 24 28"><path fill="var(--red)" d="M12 0a10 10 0 0 0-10 10c0 7.5 10 18 10 18s10-10.5 10-18A10 10 0 0 0 12 0zm0 14a4 4 0 1 1 0-8 4 4 0 0 1 0 8z"/></svg>48 Quarry Lane, Suite 3</div>
    <div style="padding-left:22px">Pinecrest, AZ 85099, USA</div>
    <div class="row"><svg width="12" height="12" viewBox="0 0 24 24"><path fill="var(--red)" d="M6.6 10.8a15 15 0 0 0 6.6 6.6l2.2-2.2c.3-.3.7-.4 1-.2 1.1.4 2.3.6 3.6.6.6 0 1 .4 1 1V20c0 .6-.4 1-1 1A17 17 0 0 1 3 4c0-.6.4-1 1-1h3.5c.6 0 1 .4 1 1 0 1.3.2 2.5.6 3.6.1.3 0 .7-.2 1z"/></svg>555.014.2200</div>
    <div class="row"><svg width="12" height="10" viewBox="0 0 24 18"><rect width="24" height="18" rx="2" fill="var(--red)"/><path d="M1 2l11 8 11-8" stroke="#2b2b2e" stroke-width="2" fill="none"/></svg>hello@krtvlabs.com</div>
  </div>
  <div class="fcol" style="left:740px">
    <h3>MENU</h3>
    <div>Home</div><div>About Us</div><div>Services</div><div>Blog</div><div>Contact Us</div>
  </div>
  <div class="fcol social" style="left:930px">
    <h3>CONNECT WITH US</h3>
    <div class="row"><span class="dot"></span>Friendbook</div>
    <div class="row"><span class="dot"></span>Chirper</div>
    <div class="row"><span class="dot"></span>Linkwork</div>
  </div>
  <div class="copyright">Copyright © 2018 All Rights Reserved</div>
</footer>

</body>
</html>
```